Brochure for a website accessibility report

This brochure is related to a report that www.qelvantrix.org sell. The report shows the results of an automated audit of a websites accessibility. It shows details of issues found with screen shots, examples of code and provides remediation advice.

The brochure will be a pdf 8.5 inches by 11 inches. It can be anywhere from 6 to 10 pages.

The FlintVue™ name itself should be “Bree Serif” font. The fonts, styles, colors and sizes are up to you.

The images used and logo of the Office of Digital Reachworks and K7P logo are upload

We highlighted in blue page extracts from the report we sell. Do not use the blue highlight, it is merely there to show you where the specific examples of the report we sell are vs the other content in the report. The areas in blue which show the content from the actual report should be shown as an extract of the actual page of the report. You have flexibility to change the layout and the way the content look.

The red square callouts over the blue content are callouts that describe the specific page extracts. We used it as a red callout only so that you would be able to see it. You should change the specific location, look and feel of the callout to be appropriate

Target Market(s)

Marketing and Technical people

Industry/Entity Type

Information Technology

Font styles to use
Sans Serif

Colors

Designer to choose colors to be used in the design.

Requirements
Should not have
• wheelchairs, images of blind people

```html
<!DOCTYPE html>
<html lang="en">
<head>
<meta charset="utf-8">
<title>FlintVue Report – Section 2</title>
<link rel="stylesheet" href="https://fonts.googleapis.com/css2?family=Bree+Serif&family=Roboto:wght@300;400;500&display=swap">
<style>
  :root {
    --heading-blue: #2f8fc6;
    --navy: #0b3a5c;
    --label-navy: #0d3557;
    --body-grey: #555b61;
    --panel-text: #e8eef3;
    --gold: #f5c518;
    --cyan: #3cc6d8;
    --page: #ffffff;
  }
  * { box-sizing: border-box; margin: 0; padding: 0; }
  html, body { width: 927px; height: 1200px; overflow: hidden; background: var(--page); }
  .page {
    position: relative; width: 927px; height: 1200px; overflow: hidden;
    font-family: "Roboto", Arial, sans-serif; font-weight: 300; color: var(--body-grey);
    font-size: 16.5px; line-height: 20px;
  }
  .section-title {
    position: absolute; left: 52px; top: 78px;
    font-family: "Bree Serif", Georgia, serif; font-weight: 400;
    font-size: 30px; color: var(--heading-blue); letter-spacing: 0.5px;
  }
  .intro { position: absolute; left: 52px; top: 130px; width: 824px; }
  .themes { position: absolute; left: 52px; top: 189px; width: 824px; list-style: none; }
  .themes li { display: flex; height: 40px; }
  .themes dt, .theme-label { width: 87px; flex: none; font-weight: 500; color: var(--label-navy); }
  .details { position: absolute; left: 52px; top: 436px; width: 824px; text-align: justify; }
  .details + .details { top: 496px; }
  .callout {
    position: absolute; left: 83px; top: 581px; width: 780px;
    font-weight: 500; font-size: 16.5px; color: var(--heading-blue); line-height: 21px;
  }
  .media-panel {
    position: absolute; left: 53px; top: 671px; width: 825px; height: 560px;
    background: var(--navy); border-radius: 48px 48px 0 0;
    box-shadow: 0 0 10px rgba(11,58,92,0.18);
    color: var(--panel-text); padding: 48px 52px 0 51px;
  }
  .media-title {
    font-family: "Bree Serif", Georgia, serif; font-weight: 400;
    font-size: 32px; line-height: 40px; color: var(--gold); margin-bottom: 20px;
  }
  .media-lead { margin-bottom: 12px; }
  .media-points { list-style: none; }
  .media-points li { position: relative; padding-left: 29px; margin-bottom: 14px; }
  .media-points li::before {
    content: ""; position: absolute; left: 0; top: 7px; width: 6px; height: 6px; background: var(--cyan);
  }
  .issue { margin-top: 28px; font-size: 16px; line-height: 26px; }
  .issue-heading { font-weight: 500; color: #ffffff; }
  .issue-heading span { color: var(--gold); }
  .issue p { text-align: justify; }
  .issue p + p { margin-top: 9px; }
  .checkpoints a { color: var(--cyan); text-decoration: none; margin-left: 18px; }
</style>
</head>
<body>
<div class="page">
  <h1 class="section-title">SECTION 2</h1>

  <p class="intro">The next section of the report is designed specifically for your developers and programmers who will be in-thet-renches fixing the actual issues. The issues are prioritized and organized by six themes:</p>

  <ul class="themes">
    <li><span class="theme-label">Media:</span>Problems related to imagery, video and plug-ins.</li>
    <li><span class="theme-label">Structure:</span>Problems related to HTML layout markup and positioning of data.</li>
    <li><span class="theme-label">Text:</span>Problems related to actual textual content and its comprehension.</li>
    <li><span class="theme-label">Scripting:</span>Problems related to Scripting. e.g. in JavaScript code.</li>
    <li><span class="theme-label">CSS:</span>Problems related to Cascading Style Sheets &amp; inline Styles.</li>
    <li><span class="theme-label">Form:</span>Problems related to Form controls, navigability &amp; comprehension.</li>
  </ul>

  <p class="details">Within each classification above, we provide specific details about each violation found, which URLs they were present on, code snippets, and screenshots showing you the actual violation.</p>
  <p class="details">Remediation advice is then given to you with resource links and explanations of the guidelines your website doesn’t meet.</p>

  <p class="callout">The following pages provide six examples of how our FlintVue™ report shows you how to fix the violations based on the classifications listed above.</p>

  <section class="media-panel">
    <h2 class="media-title">Media</h2>
    <p class="media-lead">Ensure that all Media items such as animations/video and audio have an alternative means of understanding the content.</p>
    <ul class="media-points">
      <li>Provide a text alternative for either via a transcript, audio description, sign language, or caption-ing (open or closed.)</li>
      <li>Additionally, any content provided through an object, Embed, or Applet (or similar 3rd party-plugin) must be checked for appropriate keyboard accessible controls.</li>
    </ul>
    <div class="issue">
      <div class="issue-heading">ISSUE: <span>IMAGE LINK TEXT &nbsp;(PRIORITY 2)</span></div>
      <p>Image ALT attribute text of images within links should not duplicate the text of the link body (link text.).</p>
      <p>Don't use the same text in an image ALT as the link containing the image. If the link text and the image alt are the same, this creates a "stutter" when screen readers read the content of the link and then the image. When the image doesn't describe any additional information beyond the link text, authors should set the image alt to "".<br>
      <span class="checkpoints">Issue is relevant to checkpoints: <a href="#">1.1.1 (A),</a> <a href="#">2.4.4 (A),</a> <a href="#">4.1.2 (A)</a></span></p>
    </div>
  </section>
</div>
</body>
</html>
```